Looking to Redesign Brevonix.com website

You guys did one of the brochures for brevonix.com and I would like to see if we can go ahead and get an estimate for a redesigned web site for the company. We currently have a couple of pages on brevonix.com which are very much a starter type site.

The new design will need to reflect some of the things discussed in the brochure. It will have flash. Needs to be designed for simple hosting using cpanels.

The site needs to have between 12 and 15 pages with flash pages to move through features. Integrated with twitter like it is now, and contact forms delivered from our CRM along with other interactive features such as subscription to newsletter, etc...

I don't have lots of details on how to proceed yet, but here are some competitor sites:

Can we take a look at potential costs involved in the redo of the site as vague as my description above can permit.

Target Market(s)

Business to Business

Number of Pages Required

5+ page

Font styles to use
Sans Serif

Requirements
Must have
• Must have professional feel. Similar to brochure. and logo.
• Include our story in the discussion.
• embedded links to our CRM for popup contact forms.
• Logo files and 2 types of brochures uploaded.
• Important to keep color scheme
Nice to have
• Flash and some movement
Should not have
• Not sure yet

```html
<!DOCTYPE html>
<html lang="en">
<head>
<meta charset="utf-8">
<title>Brevonix – Inter-Company Cloud Communications Platform</title>
<link rel="stylesheet" href="https://fonts.googleapis.com/css2?family=Exo+2:ital,wght@1,800&family=Raleway:wght@400;500;600;700;800&display=swap">
<style>
:root{
  --red:#c8090e;
  --red-dark:#8d0508;
  --ink:#222222;
  --charcoal:#2b2b2b;
  --grey-band:#eeeeee;
  --grey-text:#555555;
  --white:#ffffff;
  --footer:#333333;
  --footer-deep:#262626;
}
*{box-sizing:border-box;margin:0;padding:0}
html,body{width:1200px;height:3340px;overflow:hidden}
body{font-family:"Raleway",Arial,sans-serif;color:var(--ink);background:var(--white);position:relative}
.abs{position:absolute}
.wave{position:absolute;left:0;width:1200px;display:block}

/* header */
.site-header{top:0;left:0;width:1200px;height:148px;background:var(--white)}
.brand{left:76px;top:62px;display:flex;align-items:center;gap:10px}
.brand-dot{width:34px;height:34px;border-radius:50%;background:var(--red)}
.brand-name{font-weight:800;font-size:24px;color:var(--red)}
.contact-strip{top:30px;right:60px;display:flex;gap:36px}
.contact{display:flex;align-items:center;gap:10px}
.contact small{display:block;font-size:10px;color:#888;letter-spacing:.5px}
.contact b{display:block;font-size:13px;color:var(--ink);font-weight:700}
.contact .big{font-size:16px}
.contact + .contact{border-left:1px solid #ddd;padding-left:22px}
.main-nav{top:94px;right:58px;display:flex;gap:10px;align-items:center}
.main-nav a{font-size:13px;font-weight:700;color:var(--ink);text-decoration:none;padding:10px 15px;border-radius:20px}
.main-nav a.active{background:var(--red);color:var(--white);padding:10px 26px}

/* hero */
.hero{top:148px;left:0;width:1200px;height:520px;background:radial-gradient(ellipse at 55% 45%,#a0070c 0%,#5b0306 50%,#1b0102 100%)}
.hero-brand{top:140px;left:0;width:1200px;display:flex;justify-content:center;align-items:center;gap:10px}
.hero-brand .brand-dot{background:var(--white);width:40px;height:40px}
.hero-brand .brand-name{color:var(--white);font-size:26px}
.hero-title{top:214px;left:0;width:1200px;text-align:center;font-family:"Exo 2",Arial,sans-serif;font-style:italic;font-weight:800;font-size:38px;color:var(--white);letter-spacing:1px}
.hero-sub{top:266px;left:0;width:1200px;text-align:center;font-size:28px;color:var(--white);font-weight:500}
.dots{top:348px;left:76px;display:flex;gap:10px}
.dots span{width:11px;height:11px;border-radius:50%;background:var(--white)}
.dots span.on{background:var(--red)}

/* channels */
.channel{width:120px;text-align:center}
.channel .ring{width:88px;height:88px;margin:0 auto;border-radius:50%;background:var(--ink);border:4px solid var(--white);box-shadow:0 2px 6px rgba(0,0,0,.3);display:flex;align-items:center;justify-content:center}
.channel p{margin-top:14px;font-size:16px;font-weight:700;letter-spacing:1.5px;color:var(--ink);line-height:1.2}

/* shared section heads */
.sec-head{display:flex;align-items:center;gap:12px}
.sec-head .mark{width:34px;height:34px;border-radius:50%;background:#b5b5b5}
.sec-head h2{font-family:"Exo 2",Arial,sans-serif;font-style:italic;font-weight:800;font-size:28px;color:var(--red)}
.btn{display:inline-block;font-size:13px;font-weight:700;color:var(--white);padding:12px 34px;border-radius:22px;text-decoration:none}
.btn-dark{background:var(--ink)}
.btn-red{background:var(--red)}

.about{top:955px;left:76px;width:1050px}
.about p{margin-top:22px;font-size:14px;line-height:24px;color:var(--grey-text)}
.about p strong{color:var(--red);font-weight:700}
.about .btn{margin-top:26px}

/* advantages */
.adv-band{top:1250px;left:0;width:1200px;height:480px;background:var(--grey-band)}
.photo-round{border-radius:50%;border:8px solid var(--white);box-shadow:0 4px 12px rgba(0,0,0,.35)}
.adv-photo{top:1200px;left:72px;width:340px;height:340px;background:linear-gradient(135deg,#5a6f95,#c9d2e3 55,#3b4a6a)}
.adv-photo{background:linear-gradient(135deg,#4c5f86 0%,#c9d2e3 50%,#2f3c59 100%)}
.adv-copy{top:1295px;left:434px;width:720px}
.adv-copy .lead{margin-top:14px;font-size:16px;color:var(--ink)}
.adv-grid{margin-top:20px;display:grid;grid-template-columns:360px 360px;row-gap:20px}
.adv-item{display:flex;gap:16px;align-items:flex-start}
.adv-item .ico{flex:none;width:70px;height:70px;border-radius:50%;border:2px solid var(--ink);background:var(--white);display:flex;align-items:center;justify-content:center}
.adv-item h3{font-size:15px;font-weight:700;color:var(--red);margin-top:8px}
.adv-item p{font-size:13px;font-weight:600;line-height:22px;color:var(--ink);margin-top:4px}
.adv-copy .btn{margin-top:22px}

/* why */
.why-band{top:1770px;left:0;width:1200px;height:420px;background:var(--charcoal)}
.why-photo{top:1680px;left:800px;width:330px;height:330px;background:linear-gradient(140deg,#d8dde4 0%,#8e9bb0 50%,#3d4656 100%)}
.why{top:1838px;left:76px;width:700px}
.why .sec-head h2{color:var(--white)}
.why p{margin-top:18px;font-size:14px;line-height:26px;color:#e6e6e6}
.why .btn{margin-top:26px}

/* features */
.features-head{top:2210px;left:0;width:1200px;display:flex;justify-content:center}
.features-sub{top:2280px;left:0;width:1200px;text-align:center;font-size:16px;font-weight:500}
.feature{width:340px;text-align:center}
.feature .disc{width:92px;height:92px;margin:0 auto;border-radius:50%;background:radial-gradient(circle at 40% 35%,#e2161c,#a8070b);box-shadow:0 4px 10px rgba(0,0,0,.3);display:flex;align-items:center;justify-content:center}
.feature h3{margin-top:26px;font-size:17px;font-weight:500;color:var(--red)}
.feature p{margin-top:8px;font-size:13px;font-weight:500;line-height:21px;color:var(--ink)}

/* footer */
.footer{top:2960px;left:0;width:1200px;height:305px;background:linear-gradient(#3a3a3a,#2a2a2a)}
.foot-brand{top:3060px;left:76px;display:flex;gap:10px;align-items:center}
.foot-brand .brand-dot{background:var(--white)}
.foot-brand .brand-name{color:var(--white)}
.foot-about{top:3140px;left:76px;width:300px;font-size:13px;line-height:24px;color:#ddd}
.foot-about a{display:block;color:var(--white);font-weight:700;text-decoration:none}
.foot-divider{width:1px;background:#4a4a4a;top:3040px;height:200px}
.quick{top:3052px;left:465px}
.foot-title{font-size:13px;font-weight:700;letter-spacing:1px;color:var(--white)}
.quick ul{list-style:none;margin-top:18px;display:grid;grid-template-columns:166px 120px;row-gap:13px}
.quick li{font-size:13px;color:#ddd}
.newsletter{top:3052px;left:838px;width:290px}
.newsletter .field{margin-top:18px;height:38px;border-radius:19px;background:var(--white);font-size:13px;color:#666;padding:11px 18px}
.newsletter .field + .field{margin-top:12px}
.newsletter .btn{margin-top:16px;margin-left:172px;padding:11px 26px}
.bottom-bar{top:3265px;left:0;width:1200px;height:75px;background:var(--footer-deep)}
.copyright{top:3296px;left:76px;font-size:12px;color:#aaa}
.socials{top:3285px;left:1060px;display:flex;gap:10px}
.socials span{width:30px;height:30px;border-radius:50%;background:#2a8ad0}
</style>
</head>
<body>

<header class="abs site-header">
  <div class="abs brand"><span class="brand-dot"></span><span class="brand-name">Brevonix</span></div>
  <div class="abs contact-strip">
    <div class="contact">
      <svg width="24" height="26" viewBox="0 0 24 26"><circle cx="12" cy="8" r="6" fill="#222"/><path d="M2 26c0-7 4-10 10-10s10 3 10 10z" fill="#222"/></svg>
      <div><small>SUPPORT</small><b>CHAT WITH US</b></div>
    </div>
    <div class="contact">
      <svg width="24" height="18" viewBox="0 0 24 18"><rect x="1" y="1" width="22" height="16" fill="none" stroke="#222" stroke-width="2"/><path d="M1 1l11 9 11-9" fill="none" stroke="#222" stroke-width="2"/></svg>
      <div><small>EMAIL US AT</small><b>SALES@BREVONIX.COM</b></div>
    </div>
    <div class="contact">
      <svg width="20" height="22" viewBox="0 0 20 22"><path d="M4 1l4 5-2 3c1 3 3 5 6 6l3-2 4 4-3 4C8 20 1 12 1 4z" fill="#222"/></svg>
      <div><small>CALL US NOW</small><b class="big">+1 800 555 0142</b></div>
    </div>
  </div>
  <nav class="abs main-nav">
    <a class="active" href="#">HOME</a><a href="#">WHY BREVONIX</a><a href="#">BENEFITS</a><a href="#">CASE STUDIES</a><a href="#">HARDWARE</a><a href="#">ABOUT US</a>
  </nav>
</header>

<section class="abs hero" role="img" aria-label="Dark red background of connected communication symbols">
  <div class="abs hero-brand"><span class="brand-dot"></span><span class="brand-name">Brevonix</span></div>
  <h1 class="abs hero-title">DEVISE YOUR TRUTH</h1>
  <p class="abs hero-sub">Inter-Company Cloud Communications Platform</p>
  <div class="abs dots"><span class="on"></span><span></span><span></span><span></span></div>
</section>

<svg class="wave" style="top:560px" height="320" viewBox="0 0 1200 320" preserveAspectRatio="none">
  <path d="M0 60 C300 40 500 130 800 140 C1000 145 1120 90 1200 30 L1200 320 L0 320Z" fill="#1a1a1a"/>
  <path d="M0 66 C300 50 500 140 800 150 C1000 155 1120 100 1200 42 L1200 320 L0 320Z" fill="#b0070c"/>
  <path d="M0 80 C300 70 520 160 800 168 C1000 172 1120 120 1200 64 L1200 320 L0 320Z" fill="#eeeeee"/>
  <path d="M0 150 C300 120 600 260 900 250 C1050 245 1150 220 1200 200 L1200 320 L0 320Z" fill="#ffffff"/>
</svg>

<div class="abs channel" style="left:102px;top:708px"><div class="ring"><svg width="30" height="30" viewBox="0 0 30 30"><circle cx="7" cy="23" r="3.5" fill="#fff"/><path d="M4 13a13 13 0 0 1 13 13M4 4a22 22 0 0 1 22 22" fill="none" stroke="#fff" stroke-width="3.5"/></svg></div><p>WIRELESS</p></div>
<div class="abs channel" style="left:286px;top:694px"><div class="ring"><svg width="30" height="24" viewBox="0 0 30 24"><rect x="1" y="1" width="28" height="22" rx="2" fill="#fff"/><path d="M1 3l14 11 14-11" fill="none" stroke="#222" stroke-width="2.5"/></svg></div><p>EMAIL</p></div>
<div class="abs channel" style="left:464px;top:722px"><div class="ring"><svg width="28" height="30" viewBox="0 0 28 30"><rect x="2" y="10" width="24" height="18" fill="#fff"/><rect x="8" y="2" width="12" height="10" fill="#fff" stroke="#222" stroke-width="1.5"/><rect x="6" y="15" width="4" height="3" fill="#222"/><rect x="12" y="15" width="4" height="3" fill="#222"/><rect x="6" y="21" width="4" height="3" fill="#222"/><rect x="12" y="21" width="4" height="3" fill="#222"/></svg></div><p>FAX</p></div>
<div class="abs channel" style="left:645px;top:760px"><div class="ring"><svg width="30" height="26" viewBox="0 0 30 26"><ellipse cx="15" cy="11" rx="13" ry="9" fill="#fff"/><path d="M6 17l-3 8 9-5z" fill="#fff"/><circle cx="10" cy="11" r="1.6" fill="#222"/><circle cx="15" cy="11" r="1.6" fill="#222"/><circle cx="20" cy="11" r="1.6" fill="#222"/></svg></div><p>TEXT<br>MESSAGING</p></div>
<div class="abs channel" style="left:812px;top:780px"><div class="ring"><svg width="28" height="28" viewBox="0 0 28 28"><circle cx="14" cy="14" r="12" fill="#fff"/><path d="M8 8c3 2 5 1 6 4s-2 4 0 7M18 5c0 3 3 4 5 5M17 22c1-3 4-3 5-6" fill="none" stroke="#222" stroke-width="2"/></svg></div><p>WEB</p></div>
<div class="abs channel" style="left:995px;top:760px"><div class="ring"><svg width="18" height="30" viewBox="0 0 18 30"><rect x="1" y="1" width="16" height="28" rx="3" fill="#fff"/><rect x="4" y="5" width="10" height="17" fill="#222"/><circle cx="9" cy="25.5" r="1.5" fill="#222"/></svg></div><p>PHONE</p></div>

<section class="abs about">
  <div class="sec-head"><span class="mark"></span><h2>ABOUT US</h2></div>
  <p><strong>Brevonix</strong> Platform was born out of the desire to offer reliable, affordable phone systems for the small- to medium-sized business. Since 2003, we have offered hosted VOIP PBX and call routing services, but they were bundled with larger IT services. As such, it was only cost-effective for the large corporate client.</p>
  <a class="btn btn-dark" href="#">READ MORE</a>
</section>

<svg class="wave" style="top:1200px" height="100" viewBox="0 0 1200 100" preserveAspectRatio="none">
  <path d="M0 70 C300 0 700 -10 1200 40 L1200 100 L0 100Z" fill="#eeeeee"/>
  <path d="M300 30 C600 -5 900 0 1200 30 L1200 75 C950 35 650 25 300 30Z" fill="#222"/>
  <path d="M600 30 C850 25 1050 40 1200 58 L1200 80 C1000 62 800 45 600 30Z" fill="#c8090e"/>
</svg>
<div class="abs adv-band"></div>
<div class="abs photo-round adv-photo" role="img" aria-label="Photo of a businessman drawing a cloud network on a screen"></div>

<section class="abs adv-copy">
  <div class="sec-head"><span class="mark"></span><h2>ADVANTAGES</h2></div>
  <p class="lead">Discovering your needs, creating solutions that truly work</p>
  <div class="adv-grid">
    <div class="adv-item"><span class="ico"><svg width="22" height="28" viewBox="0 0 22 28"><path d="M1 1h14l6 6v20H1z" fill="#c8090e"/><path d="M5 14h12M5 18h12M5 22h8" stroke="#fff" stroke-width="2"/></svg></span><div><h3>Quick ROI</h3><p>Equipment is included in the<br>service..</p></div></div>
    <div class="adv-item"><span class="ico"><svg width="24" height="28" viewBox="0 0 24 28"><path d="M12 1l11 4v8c0 7-5 12-11 14C6 25 1 20 1 13V5z" fill="#c8090e"/><path d="M12 5v18" stroke="#fff" stroke-width="2"/></svg></span><div><h3>Secure</h3><p>Encrypted lines</p></div></div>
    <div class="adv-item"><span class="ico"><svg width="30" height="28" viewBox="0 0 30 28"><circle cx="11" cy="17" r="7" fill="none" stroke="#c8090e" stroke-width="5" stroke-dasharray="3 2"/><circle cx="23" cy="7" r="4.5" fill="none" stroke="#c8090e" stroke-width="3.5" stroke-dasharray="2 1.5"/></svg></span><div><h3>Easy installation</h3><p>Very little business<br>interruption</p></div></div>
    <div class="adv-item"><span class="ico"><svg width="26" height="26" viewBox="0 0 26 26"><circle cx="13" cy="13" r="11" fill="none" stroke="#c8090e" stroke-width="3"/><path d="M13 6v8h5" fill="none" stroke="#c8090e" stroke-width="3"/></svg></span><div><h3>Expandable</h3><p>One unit at a time</p></div></div>
  </div>
  <a class="btn btn-dark" href="#">READ MORE</a>
</section>

<svg class="wave" style="top:1690px" height="110" viewBox="0 0 1200 110" preserveAspectRatio="none">
  <path d="M0 0 L1200 0 L1200 60 C900 100 500 20 0 30Z" fill="#eeeeee"/>
  <path d="M0 30 C500 20 900 100 1200 60 L1200 110 L0 110Z" fill="#2b2b2b"/>
  <path d="M0 30 C400 22 800 70 1100 80 C500 70 300 40 0 58Z" fill="#c8090e"/>
</svg>
<div class="abs why-band"></div>
<div class="abs photo-round why-photo" role="img" aria-label="Photo of a smiling business team at a laptop"></div>

<section class="abs why">
  <div class="sec-head"><span class="mark"></span><h2>WHY BREVONIX</h2></div>
  <p>Honestly, your office phone system is probably the least sexy thing in your company – the minute the system is down, you're out of business – so you need a phone system that you can count on every minute of every day. But your phone system doesn't have to be boring, it can look great, too! With a sleek design and customized logos, these phones add a distinctive look sitting on the desk. What is even better, is how good this system makes you look to your customers. Whatever image you want to portray.</p>
  <a class="btn btn-red" href="#">READ MORE</a>
</section>

<svg class="wave" style="top:2120px" height="100" viewBox="0 0 1200 100" preserveAspectRatio="none">
  <path d="M0 0 L1200 0 L1200 30 C900 110 400 60 0 40Z" fill="#2b2b2b"/>
</svg>

<div class="abs features-head sec-head"><span class="mark"></span><h2>FEATURES</h2></div>
<p class="abs features-sub">Unified Communications Sample of Powerful Feature Sets</p>

<div class="abs feature" style="left:70px;top:2345px"><div class="disc"><svg width="32" height="28" viewBox="0 0 32 28"><path d="M2 4h10v4H6v12h6v4H2z" fill="#fff"/><path d="M12 10h10V4l9 10-9 10v-6H12z" fill="#fff"/></svg></div><h3>Outgoing Call Redundancies</h3><p>Multiple Telecommunications Providers create<br>excellent service redundancies<br>for outgoing calls.</p></div>
<div class="abs feature" style="left:430px;top:2345px"><div class="disc"><svg width="32" height="28" viewBox="0 0 32 28"><path d="M20 4h10v20H20v-4h6V8h-6z" fill="#fff"/><path d="M2 10h10V4l9 10-9 10v-6H2z" fill="#fff"/></svg></div><h3>Incoming Call Redundancies</h3><p>Multiple Telecommunications Providers create<br>excellent service redundancies<br>for outgoing calls.</p></div>
<div class="abs feature" style="left:790px;top:2345px"><div class="disc"><svg width="30" height="30" viewBox="0 0 30 30"><path d="M24 10A10 10 0 0 0 6 12M6 20a10 10 0 0 0 18-2" fill="none" stroke="#fff" stroke-width="4"/><path d="M20 4l7 1-1 7zM10 26l-7-1 1-7z" fill="#fff"/></svg></div><h3>Implementation Ease</h3><p>Multiple Telecommunications Providers create<br>excellent service redundancies<br>for outgoing calls.</p></div>

<div class="abs feature" style="left:70px;top:2610px"><div class="disc"><svg width="28" height="30" viewBox="0 0 28 30"><path d="M14 2c6 0 9 4 9 10v6l3 5H2l3-5v-6c0-6 3-10 9-10z" fill="#fff"/><circle cx="14" cy="26" r="3" fill="#fff"/></svg></div><h3>911 Notification</h3><p>Multiple Telecommunications Providers create<br>excellent service redundancies<br>for outgoing calls.</p></div>
<div class="abs feature" style="left:430px;top:2610px"><div class="disc"><svg width="28" height="28" viewBox="0 0 20 22"><path d="M4 1l4 5-2 3c1 3 3 5 6 6l3-2 4 4-3 4C8 20 1 12 1 4z" fill="#fff"/></svg></div><h3>Advanced Call Management</h3><p>Multiple Telecommunications Providers create<br>excellent service redundancies<br>for outgoing calls.</p></div>
<div class="abs feature" style="left:790px;top:2610px"><div class="disc"><svg width="24" height="32" viewBox="0 0 24 32"><rect x="7" y="1" width="10" height="18" rx="5" fill="#fff"/><path d="M3 14a9 9 0 0 0 18 0M12 23v6M7 30h10" fill="none" stroke="#fff" stroke-width="2.5"/></svg></div><h3>Advanced Voicemail</h3><p>Multiple Telecommunications Providers create<br>excellent service redundancies<br>for outgoing calls.</p></div>

<svg class="wave" style="top:2830px" height="140" viewBox="0 0 1200 140" preserveAspectRatio="none">
  <path d="M0 20 C300 90 800 100 1200 50 L1200 140 L0 140Z" fill="#8d0508"/>
  <path d="M0 0 C300 70 800 80 1200 30 L1200 110 C800 130 300 110 0 60Z" fill="#c8090e"/>
  <path d="M0 60 C300 110 800 130 1200 110 L1200 140 L0 140Z" fill="#3a3a3a"/>
  <path d="M0 76 C300 120 800 132 1200 118 L1200 140 L0 140Z" fill="#2f2f2f"/>
</svg>

<footer class="abs footer"></footer>
<div class="abs foot-brand"><span class="brand-dot"></span><span class="brand-name">Brevonix</span></div>
<p class="abs foot-about">Inter-Company Cloud Communications Platform..<a href="#">Read More</a></p>
<div class="abs foot-divider" style="left:435px"></div>
<div class="abs foot-divider" style="left:808px"></div>
<div class="abs quick">
  <p class="foot-title">QUICK LINKS</p>
  <ul><li>Home</li><li>Hardware</li><li>Why Brevonix</li><li>About Us</li><li>Benefits</li><li>Contact Us</li><li>Case Studies</li></ul>
</div>
<div class="abs newsletter">
  <p class="foot-title">NEWSLETTER SIGN UP</p>
  <div class="field">Enter Name</div>
  <div class="field">Enter Email Address</div>
  <a class="btn btn-red" href="#">SIGN UP</a>
</div>
<div class="abs bottom-bar"></div>
<p class="abs copyright">© 2015-2016 brevonix. All Rights Reserved.</p>
<div class="abs socials"><span></span><span></span></div>

</body>
</html>
```